Photography Business, Business Card

Looking for a unique cutting edge card that takes advantage of the latest printing technologies. Please review this site for all the options they office: https://glowprintly.com. If you can think it they can do it. And if you have an idea and do not know if they can do it, I will check into it.

Target Market(s)

People and places I took images of and future clients.

Industry/Entity Type

Photography

Contact Information for Business Card

Name, cell & email. Derek Holloway, dholloway@kpnvisuals.com, 312-748-2961

Colors

Designer to choose only greyscale colors for use in the design.

Requirements
Must have
• 100% cutting edge. Is so great, those I hand it to always show it to someone else. A piece of art.
Nice to have
• Blacks, silvers, greys, some red. Maybe other colors?

```html
<!DOCTYPE html>
<html lang="en">
<head>
<meta charset="UTF-8">
<title>Derek Holloway Photography – Business Card</title>
<link rel="stylesheet" href="https://fonts.googleapis.com/css2?family=Mrs+Saint+Delafield&family=Montserrat:wght@400;500;700&display=swap">
<style>
  :root {
    --page-bg: #e6e6e6;
    --card-dark: #0d0d0f;
    --card-mid: #2a2a2e;
    --ink-light: #f2f2f2;
    --ink-muted: #b8b8bc;
    --accent-red: #e3262c;
    --frame-grey: #8a8a8e;
    --lens-deep: #07090c;
    --lens-glow: #3b4a5c;
  }
  * { margin: 0; padding: 0; box-sizing: border-box; }
  html, body {
    width: 800px; height: 1200px; overflow: hidden;
    background: var(--page-bg);
    font-family: "Montserrat", sans-serif;
  }
  .sheet {
    position: relative; width: 800px; height: 1200px;
    display: flex; flex-direction: column; align-items: center; justify-content: center;
    gap: 70px;
  }
  .card {
    position: relative; width: 680px; height: 389px;
    border-radius: 6px; overflow: hidden;
    background: radial-gradient(ellipse at 75% 40%, var(--card-mid) 0%, var(--card-dark) 65%);
    box-shadow: 0 6px 18px rgba(0,0,0,0.18);
  }
  .signature {
    position: absolute; left: 60px; top: 30px;
    font-family: "Mrs Saint Delafield", cursive;
    font-size: 62px; line-height: 1; color: var(--ink-light);
    white-space: nowrap;
  }
  .signature-sub {
    position: absolute; left: 170px; top: 100px;
    font-size: 9px; letter-spacing: 3px; font-weight: 500;
    color: var(--ink-muted);
  }
  .brand-name {
    position: absolute; left: 64px;
    font-weight: 700; font-size: 38px; letter-spacing: 2px; line-height: 1;
    color: var(--accent-red);
  }
  .front .brand-name { top: 180px; }
  .back .brand-name { top: 300px; font-size: 32px; }
  .front .aperture {
    position: absolute; right: -60px; top: -20px;
    width: 430px; height: 430px; border-radius: 50%;
    background: radial-gradient(circle, rgba(80,80,88,0.35) 0%, rgba(40,40,44,0.2) 45%, rgba(0,0,0,0) 70%);
  }
  .front .brackets, .back .lens-art { position: absolute; left: 0; top: 0; }
  .contact-list {
    position: absolute; left: 62px; top: 172px;
    list-style: none; display: flex; flex-direction: column; gap: 16px;
  }
  .contact-item {
    display: flex; align-items: center; gap: 10px;
    font-size: 13px; color: var(--ink-light); font-weight: 500;
  }
  .contact-icon {
    width: 20px; height: 20px; border-radius: 50%;
    background: var(--accent-red);
    display: flex; align-items: center; justify-content: center;
  }
</style>
</head>
<body>
<main class="sheet">

  <section class="card front" aria-label="Card front">
    <div class="aperture" role="img" aria-label="Faint camera aperture blades decoration"></div>
    <svg class="brackets" width="680" height="389" viewBox="0 0 680 389" fill="none" stroke="var(--frame-grey)" stroke-width="2">
      <path d="M50 205 V150 H90"/>
      <path d="M260 190 V245 H220"/>
    </svg>
    <div class="signature">Derek Holloway</div>
    <div class="signature-sub">PHOTOGRAPHY</div>
    <div class="brand-name">DXH</div>
  </section>

  <section class="card back" aria-label="Card back">
    <svg class="lens-art" width="680" height="389" viewBox="0 0 680 389">
      <defs>
        <radialGradient id="lensFill" cx="50%" cy="45%" r="55%">
          <stop offset="0%" stop-color="var(--lens-glow)"/>
          <stop offset="55%" stop-color="#1a2028"/>
          <stop offset="100%" stop-color="var(--lens-deep)"/>
        </radialGradient>
      </defs>
      <path d="M520 38 H620 Q632 38 632 50 V200" fill="none" stroke="var(--accent-red)" stroke-width="3"/>
      <path d="M402 200 V338 Q402 350 414 350 H500" fill="none" stroke="var(--accent-red)" stroke-width="3"/>
      <circle cx="505" cy="194" r="112" fill="url(#lensFill)" role="img" aria-label="Photograph of a camera lens"/>
      <circle cx="505" cy="194" r="118" fill="none" stroke="var(--ink-light)" stroke-width="7"/>
    </svg>
    <div class="signature">Derek Holloway</div>
    <div class="signature-sub">PHOTOGRAPHY</div>
    <ul class="contact-list">
      <li class="contact-item">
        <span class="contact-icon">
          <svg width="11" height="11" viewBox="0 0 24 24" fill="#fff"><path d="M6.6 10.8a15.1 15.1 0 0 0 6.6 6.6l2.2-2.2a1 1 0 0 1 1-.25 11.4 11.4 0 0 0 3.6.6 1 1 0 0 1 1 1V20a1 1 0 0 1-1 1A17 17 0 0 1 3 4a1 1 0 0 1 1-1h3.5a1 1 0 0 1 1 1c0 1.250.2 2.45.6 3.6a1 1 0 0 1-.25 1z"/></svg>
        </span>
        312-748-2961
      </li>
      <li class="contact-item">
        <span class="contact-icon">
          <svg width="11" height="11" viewBox="0 0 24 24" fill="none" stroke="#fff" stroke-width="2.4"><rect x="3" y="5" width="18" height="14" rx="2"/><path d="M3 7l9 6 9-6"/></svg>
        </span>
        dholloway@kpnvisuals.com
      </li>
    </ul>
    <div class="brand-name">DXH</div>
  </section>

</main>
</body>
</html>
```